Custom Wordpress Theme - Original and Professional

We are a boutique IT consulting firm that provide small and medium business in Australia three different levels of IT service.
We are looking for a developer who will create a customised, original and professional wordpress theme. We are looking for the developer to create a professional, clean, clear and simple theme with a stylish layout, images and icons.
Our three services are: IT support | IT Services | IT Solutions and we would like to clearly differentiate the difference in each level of service in as few words as possible.
IT Support is the ad hock “call us, when you need us” service, that smaller business or those with minimal issues use.
IT service is the unlimited service, that business with existing (and well maintained) IT systems choose and is both flexible and scalable including no contracts or paperwork required.
IT solutions are the unlimited service that businesses that need new or updated infrastructure choose and it includes all the hardware, software and services with no contracts or any ongoing commitment.
The main page on the web site will attract the visitor to choose the right “service level” for their business and then we will have a dedicated page for each service and another page for a comparison (table) to compare all three services.
Lastly we will need a contact us page that has both office locations (Sydney and Melbourne), contact phone numbers and an email form.
Items we are focused on for this project are: 1. Images, 2.Icons 3. Layout.
In summary we are looking for a custom WordPress theme into a 6 page (Home, IT Support, IT Services, IT Solutions, Compare Service levels and Contact us) website. The design must include relevant images and icons and be clear, simple, professional and sleek.

Thank you for your time and creativity and I look forward to working with you!

Target Market(s)

Small and Medium businesses in Australia

Industry/Entity Type

Boutique

Requirements
Must have
• - 6 Pages layout: Home, IT support, IT services, IT Solutions, Compare service levels and Contact us
- Images, Layout and Icons.
- Clean, Clear, Simple, Elegant, Stylish.
Nice to have
• - Some text (if possible but not required).
Should not have
• - Complexity.
- Confusing layout.
- Generic non matching images and icons.

```html
<!DOCTYPE html>
<html lang="en">
<head>
<meta charset="utf-8">
<title>IT Services</title>
<link href="https://fonts.googleapis.com/css2?family=Marcellus&family=Noto+Sans:ital,wght@0,400;1,400&display=swap" rel="stylesheet">
<style>
  :root {
    --ink: #111111;
    --muted: #8a8a8a;
    --accent: #3de0e3;
    --link: #2ccfd6;
    --arrow: #e84a4a;
    --rule: #9a9a9a;
    --paper: #ffffff;
    --hero-light: #e6eef2;
    --hero-mid: #b9ccd6;
    --hero-deep: #8eaabb;
  }
  * { margin: 0; padding: 0; box-sizing: border-box; }
  html, body { width: 840px; height: 1200px; overflow: hidden; background: var(--paper); }
  body { position: relative; font-family: "Noto Sans", Arial, sans-serif; color: var(--ink); }

  .brand { position: absolute; left: 45px; top: 54px; }
  .brand-name { font-family: "Marcellus", Georgia, serif; font-size: 22px; letter-spacing: 0.5px; color: var(--ink); line-height: 1; }
  .brand-slogan { font-size: 8px; color: var(--muted); margin: 9px 0 0 19px; letter-spacing: 0.2px; }

  .main-nav { position: absolute; top: 63px; left: 0; width: 840px; height: 16px; font-size: 12px; }
  .main-nav a { position: absolute; color: var(--ink); text-decoration: none; white-space: nowrap; }
  .main-nav a.current { color: var(--accent); }

  .header-rule { position: absolute; left: 36px; top: 118px; width: 770px; height: 1px; background: var(--rule); }

  .hero { position: absolute; left: 18px; top: 121px; width: 788px; height: 270px;
    background: linear-gradient(100deg, var(--hero-light) 0%, var(--hero-mid) 45%, var(--hero-light) 70%, var(--hero-deep) 100%); }

  .page-title { position: absolute; left: 50px; top: 410px; font-family: "Marcellus", Georgia, serif; font-size: 12px; color: #444; letter-spacing: 0.3px; }
  .breadcrumb { position: absolute; left: 51px; top: 430px; font-size: 7px; font-style: italic; color: var(--ink); }
  .breadcrumb .here { color: var(--accent); }

  .content { position: absolute; left: 45px; top: 519px; width: 533px; font-size: 12px; line-height: 20.2px; text-align: justify; }
  .content p + p { margin-top: 20px; }

  .sidebar-list { position: absolute; left: 606px; list-style: none; font-size: 7.5px; color: var(--link); }
  .sidebar-list li { position: absolute; left: 0; white-space: nowrap; padding-left: 11px; }
  .sidebar-list li svg { position: absolute; left: 0; top: 1px; }

  .site-footer { position: absolute; left: 0; top: 1153px; width: 840px; height: 47px; background: var(--accent); }
  .copyright { position: absolute; left: 54px; top: 15px; font-size: 12px; color: var(--paper); }
  .social { position: absolute; right: 41px; top: 19px; display: flex; gap: 4px; }
  .social span { width: 7px; height: 7px; border-radius: 50%; background: var(--paper); }
</style>
</head>
<body>
  <header>
    <div class="brand">
      <div class="brand-name">COMPANY NAME</div>
      <div class="brand-slogan">YOUR COMPANY SOLGAN</div>
    </div>
    <nav class="main-nav">
      <a style="left:352px">Home</a>
      <a style="left:403px">IT support</a>
      <a class="current" style="left:475px">IT Services</a>
      <a style="left:549px">IT Solutions</a>
      <a style="left:628px">Compare Service</a>
      <a style="left:733px">Contact us</a>
    </nav>
    <div class="header-rule"></div>
  </header>

  <div class="hero" role="img" aria-label="Photo of a woman in safety glasses touching a futuristic translucent interface screen"></div>

  <h1 class="page-title">IT SERVICES</h1>
  <div class="breadcrumb">HOME | <span class="here">IT SERVICES</span></div>

  <main class="content">
    <p>Lorem ipsum dolor sit amet, consectetur adipiscing elit. Praesent nec euismod diam, ac gravida elit. In ac sagittis velit. Integer aliquet arcu ut dapibus bibendum. Donec non sodales purus. Maecenas in ipsum id ligula tempus egestas non at diam. Pellentesque sed lectus nisi. Sed commodo nunc lorem, quis pharetra tortor feugiat quis. Nullam in nisi suscipit nisi luctus semper. Proin hendrerit mauris non tempor facilisis. Pellentesque nec metus interdum, gravida erat sed, malesuada felis. Cras tincidunt nisi et auctor pellentesque. Donec sed augue in elit gravida mollis. Nam imperdiet lectus nec sapien consequat fringilla non sed lacus. Nam porta accumsan eros, id scelerisque nunc varius eget.</p>
    <p>Aliquam erat volutpat. Donec a leo dictum, dictum elit et, ornare lacus. Mauris tempor lacus est, quis cursus ipsum venenatis eget. Proin sollicitudin tristique sem ac faucibus. Pellentesque ut dignissim dui. Pellentesque gravida at velit id aliquet. Sed adipiscing varius mollis. In convallis hendrerit leo id gravida. Suspendisse facilisis blandit nisl eget blandit. Sed sit amet dignissim risus, ac luctus eros. Curabitur egestas vestibulum lacus. Etiam id vulputate turpis. Phasellus diam magna, pulvinar eget felis convallis, tincidunt rutrum purus. Morbi erat risus, cursus eleifend leo et, sagittis vestibulum risus. Ut vel dolor ac enim porttitor aliquet.</p>
  </main>

  <ul class="sidebar-list" style="top:0">
    <li style="top:519px"><svg width="7" height="9" viewBox="0 0 7 9"><path d="M1 0 L6 4.5 L1 9 L0 7 L3 4.5 L0 2 Z" fill="var(--arrow)"/></svg>Aenean nonummy hendrerit ma</li>
    <li style="top:541px"><svg width="7" height="9" viewBox="0 0 7 9"><path d="M1 0 L6 4.5 L1 9 L0 7 L3 4.5 L0 2 Z" fill="var(--arrow)"/></svg>Fusce suscipit varius mi</li>
    <li style="top:563px"><svg width="7" height="9" viewBox="0 0 7 9"><path d="M1 0 L6 4.5 L1 9 L0 7 L3 4.5 L0 2 Z" fill="var(--arrow)"/></svg>Cum sociis natoque penatibus</li>
    <li style="top:585px"><svg width="7" height="9" viewBox="0 0 7 9"><path d="M1 0 L6 4.5 L1 9 L0 7 L3 4.5 L0 2 Z" fill="var(--arrow)"/></svg>Fusce feugiat malesuada odio</li>
    <li style="top:608px"><svg width="7" height="9" viewBox="0 0 7 9"><path d="M1 0 L6 4.5 L1 9 L0 7 L3 4.5 L0 2 Z" fill="var(--arrow)"/></svg>Morbi nunc odio, gravida</li>
    <li style="top:632px"><svg width="7" height="9" viewBox="0 0 7 9"><path d="M1 0 L6 4.5 L1 9 L0 7 L3 4.5 L0 2 Z" fill="var(--arrow)"/></svg>Morbi nunc odio, gravida</li>
    <li style="top:688px"><svg width="7" height="9" viewBox="0 0 7 9"><path d="M1 0 L6 4.5 L1 9 L0 7 L3 4.5 L0 2 Z" fill="var(--arrow)"/></svg>Aenean nonummy hendrerit ma</li>
    <li style="top:710px"><svg width="7" height="9" viewBox="0 0 7 9"><path d="M1 0 L6 4.5 L1 9 L0 7 L3 4.5 L0 2 Z" fill="var(--arrow)"/></svg>Fusce suscipit varius mi</li>
    <li style="top:732px"><svg width="7" height="9" viewBox="0 0 7 9"><path d="M1 0 L6 4.5 L1 9 L0 7 L3 4.5 L0 2 Z" fill="var(--arrow)"/></svg>Cum sociis natoque penatibus</li>
    <li style="top:754px"><svg width="7" height="9" viewBox="0 0 7 9"><path d="M1 0 L6 4.5 L1 9 L0 7 L3 4.5 L0 2 Z" fill="var(--arrow)"/></svg>Fusce feugiat malesuada odio</li>
    <li style="top:778px"><svg width="7" height="9" viewBox="0 0 7 9"><path d="M1 0 L6 4.5 L1 9 L0 7 L3 4.5 L0 2 Z" fill="var(--arrow)"/></svg>Morbi nunc odio, gravida</li>
    <li style="top:801px"><svg width="7" height="9" viewBox="0 0 7 9"><path d="M1 0 L6 4.5 L1 9 L0 7 L3 4.5 L0 2 Z" fill="var(--arrow)"/></svg>Morbi nunc odio, gravida</li>
  </ul>

  <footer class="site-footer">
    <div class="copyright">IT SOLUTION© 2013 • Privacy Policy</div>
    <div class="social" aria-label="Social links"><span></span><span></span><span></span><span></span></div>
  </footer>
</body>
</html>
```